Webdesign für Projektmanagement
Zielgruppe
Projektmanagement und Projektsteuerung von Bauvorhaben für Projektentwickler und Bauträger.
Wesentliche Bereiche sind Wirtschaftliche Steuerung, Steuerung der Baustelle und Bauabläufe sowie Steuerung der Marketing und Vertriebsaktivitäten.
Aufgabenstellung
Orientierung am Logo. Logo und Visitenkarte liegen bei. Schriftart Prelo und Prelo Slab.

```html
<!DOCTYPE html>
<html lang="de">
<head>
<meta charset="utf-8">
<title>Veldhaus Projektbau – Startseite Varianten</title>
<link href="https://fonts.googleapis.com/css2?family=Raleway:ital,wght@0,200;0,400;0,600;0,700;0,800;1,400&display=swap" rel="stylesheet">
<style>
:root{
  --navy:#03243f;
  --navy-deep:#022239;
  --gold:#a58c45;
  --white:#ffffff;
  --card:#f1f1f1;
  --text:#3a3a3a;
  --muted:#7a7a7a;
  --line:#ececec;
}
*{margin:0;padding:0;box-sizing:border-box}
html,body{width:701px;height:1200px;overflow:hidden}
body{background:var(--navy-deep);font-family:"Raleway",sans-serif;position:relative}
.screen{position:absolute;left:20px;width:663px;height:381px;overflow:hidden;background:var(--white)}
.screen--one{top:12px}
.screen--two{top:409px;left:19.5px}
.screen--three{top:806px;left:19.5px}

.sidebar{position:absolute;left:0;top:0;width:101px;height:100%;background:var(--white)}
.brand{position:absolute;left:15px;top:44px;display:flex;align-items:center;gap:4px}
.brand__mark{width:6px;height:6px;background:var(--gold)}
.brand__name{font-weight:800;font-size:14px;color:var(--navy);letter-spacing:-.2px}
.nav{position:absolute;left:0;top:93px;width:101px;list-style:none;border-top:1px solid var(--line)}
.nav__item{height:20.3px;border-bottom:1px solid var(--line);display:flex;align-items:center;justify-content:space-between;padding:0 10px 0 15.5px;font-size:5.7px;color:var(--navy);letter-spacing:.2px}
.nav__item--active{color:var(--gold);font-weight:700}
.nav__item svg{width:4px;height:4px}
.nav__search{font-style:italic;color:var(--muted);justify-content:flex-start;gap:5px}
.social{position:absolute;left:25px;top:362px;display:flex;gap:8px}
.social__dot{width:6px;height:6px;border-radius:50%;background:var(--navy)}

.hero{position:absolute;left:101px;top:0;width:562px;height:100%}
.hero__photo{position:absolute;inset:0}
.screen--one .hero__photo{background:linear-gradient(120deg,#c9bd8e 0%,#b9a96a 40%,#c8b25a 65%,#9c8d5a 100%)}
.screen--two .hero__photo{background:linear-gradient(130deg,#bfb483 0%,#c4b88c 45%,#b3a668 75%,#a89a5e 100%)}
.screen--three .hero__photo{background:linear-gradient(125deg,#c2b686 0%,#c7b67a 45%,#b9a76a 70%,#a2966a 100%)}
.topbar{position:absolute;left:0;top:0;width:100%;height:19px;background:rgba(125,112,70,.42);display:flex;align-items:center;padding-left:35px;gap:11px;font-size:5.4px;color:var(--white)}
.topbar__item{display:flex;align-items:center;gap:3px}
.topbar__item svg{width:6px;height:6px}
.hero__kicker{position:absolute;left:35px;top:97px;font-size:9.6px;font-weight:700;color:var(--navy);letter-spacing:.3px}
.hero__title{position:absolute;left:34px;top:115px;font-size:30px;font-weight:200;line-height:37px;color:var(--white);letter-spacing:.5px}
.cards{position:absolute;left:35px;top:214px;display:flex;gap:6.3px}
.card{position:relative;width:132.5px;height:93px;background:var(--card);padding:7px 8px 0}
.card__label{font-size:5.2px;font-style:italic;color:var(--muted)}
.card__title{margin-top:5px;font-size:6.2px;font-weight:600;color:var(--gold);line-height:8.3px}
.card__text{margin-top:4px;font-size:5.3px;color:var(--text);line-height:8.6px}
.card__button{position:absolute;right:0;bottom:0;width:50.5px;height:13px;background:var(--navy);color:var(--white);font-size:4.8px;font-weight:700;display:flex;align-items:center;justify-content:center;letter-spacing:.2px}
.footer{position:absolute;left:0;top:358px;width:100%;height:23px;background:rgba(235,230,205,.45);display:flex;align-items:center;padding-left:35px;font-size:5.6px;color:var(--text)}
</style>
</head>
<body>

<!-- Screen variant one -->
<section class="screen screen--one">
  <aside class="sidebar">
    <div class="brand"><span class="brand__name">Veldhaus</span><span class="brand__mark"></span></div>
    <ul class="nav">
      <li class="nav__item nav__item--active">HOME</li>
      <li class="nav__item">LEISTUNGEN</li>
      <li class="nav__item">ÜBER UNS<svg viewBox="0 0 4 4"><path d="M1 .5 2.8 2 1 3.5" fill="none" stroke="#888" stroke-width=".5"/></svg></li>
      <li class="nav__item">PROJEKTE<svg viewBox="0 0 4 4"><path d="M1 .5 2.8 2 1 3.5" fill="none" stroke="#888" stroke-width=".5"/></svg></li>
      <li class="nav__item">PARTNER</li>
      <li class="nav__item">KONTAKT</li>
      <li class="nav__item nav__search"><svg viewBox="0 0 4 4"><circle cx="1.6" cy="1.6" r="1.1" fill="none" stroke="#a58c45" stroke-width=".6"/><path d="M2.4 2.4 3.6 3.6" stroke="#a58c45" stroke-width=".6"/></svg>Suchen</li>
    </ul>
    <div class="social"><span class="social__dot"></span><span class="social__dot"></span><span class="social__dot"></span><span class="social__dot"></span></div>
  </aside>
  <main class="hero">
    <div class="hero__photo" role="img" aria-label="Foto: Schutzhelm, Wasserwaage und Baupläne auf einem Schreibtisch, goldgelb getönt"></div>
    <div class="topbar">
      <span class="topbar__item"><svg viewBox="0 0 6 6"><path d="M1.2.6 2.2.5 2.6 1.9 2 2.4Q2.6 3.5 3.6 4L4.1 3.4 5.5 3.8 5.4 4.8Q3 5.2 1 2.6Z" fill="#03243f"/></svg>+49 (0)000 - 123 456 78</span>
      <span class="topbar__item"><svg viewBox="0 0 6 6"><circle cx="3" cy="3" r="2.4" fill="none" stroke="#03243f" stroke-width=".6"/><path d="M3 1.6V3H4.2" fill="none" stroke="#03243f" stroke-width=".6"/></svg>Mo - Fr 9:00 - 18:00</span>
      <span class="topbar__item"><svg viewBox="0 0 6 6"><rect x=".5" y="1.3" width="5" height="3.4" fill="none" stroke="#03243f" stroke-width=".6"/><path d="M.5 1.3 3 3.2 5.5 1.3" fill="none" stroke="#03243f" stroke-width=".6"/></svg>info@veldhaus-bau.de</span>
      <span class="topbar__item"><svg viewBox="0 0 6 6"><path d="M3 5.8 1.3 3A1.9 1.9 0 1 1 4.7 3Z" fill="#03243f"/><circle cx="3" cy="2.2" r=".6" fill="#fff"/></svg>Lindenallee 12, 40000 Musterstadt</span>
    </div>
    <p class="hero__kicker">PROJEKTMANAGEMENT &amp; PROJEKTSTEUERUNG</p>
    <h1 class="hero__title">WIR REALISIEREN<br>BAUVORHABEN</h1>
    <div class="cards">
      <article class="card"><p class="card__label">Betriebswirtschaftliche Planung</p><h2 class="card__title">STET CLITA KASD GUBERGREN NO SEA TAKIMATA SANCTUS EST LOREM</h2><p class="card__text">Lorem ipsum dolor sit amet, consetetur sadipscing elitr, sed diam nonumy eirmod tempor invidunt ut labore et dolore magna aliquyam erat, sed diam voluptua.</p><span class="card__button">WEITERLESEN</span></article>
      <article class="card"><p class="card__label">Steuerung der baulichen Umsetzung</p><h2 class="card__title">STET CLITA KASD GUBERGREN NO SEA TAKIMATA SANCTUS EST LOREM</h2><p class="card__text">Lorem ipsum dolor sit amet, consetetur sadipscing elitr, sed diam nonumy eirmod tempor invidunt ut labore et dolore magna aliquyam erat, sed diam voluptua.</p><span class="card__button">WEITERLESEN</span></article>
      <article class="card"><p class="card__label">Marketing und Vertrieb</p><h2 class="card__title">STET CLITA KASD GUBERGREN NO SEA TAKIMATA SANCTUS EST LOREM</h2><p class="card__text">Lorem ipsum dolor sit amet, consetetur sadipscing elitr, sed diam nonumy eirmod tempor invidunt ut labore et dolore magna aliquyam erat, sed diam voluptua.</p><span class="card__button">WEITERLESEN</span></article>
    </div>
    <footer class="footer">© 2017 Veldhaus Projektbau GmbH - Impressum</footer>
  </main>
</section>

<!-- Screen variant two -->
<section class="screen screen--two">
  <aside class="sidebar">
    <div class="brand"><span class="brand__name">Veldhaus</span><span class="brand__mark"></span></div>
    <ul class="nav">
      <li class="nav__item nav__item--active">HOME</li>
      <li class="nav__item">LEISTUNGEN</li>
      <li class="nav__item">ÜBER UNS<svg viewBox="0 0 4 4"><path d="M1 .5 2.8 2 1 3.5" fill="none" stroke="#888" stroke-width=".5"/></svg></li>
      <li class="nav__item">PROJEKTE<svg viewBox="0 0 4 4"><path d="M1 .5 2.8 2 1 3.5" fill="none" stroke="#888" stroke-width=".5"/></svg></li>
      <li class="nav__item">PARTNER</li>
      <li class="nav__item">KONTAKT</li>
      <li class="nav__item nav__search"><svg viewBox="0 0 4 4"><circle cx="1.6" cy="1.6" r="1.1" fill="none" stroke="#a58c45" stroke-width=".6"/><path d="M2.4 2.4 3.6 3.6" stroke="#a58c45" stroke-width=".6"/></svg>Suchen</li>
    </ul>
    <div class="social"><span class="social__dot"></span><span class="social__dot"></span><span class="social__dot"></span><span class="social__dot"></span></div>
  </aside>
  <main class="hero">
    <div class="hero__photo" role="img" aria-label="Foto: Laptop, Stifte und Bauzeichnungen auf einem Arbeitstisch, goldgelb getönt"></div>
    <div class="topbar">
      <span class="topbar__item"><svg viewBox="0 0 6 6"><path d="M1.2.6 2.2.5 2.6 1.9 2 2.4Q2.6 3.5 3.6 4L4.1 3.4 5.5 3.8 5.4 4.8Q3 5.2 1 2.6Z" fill="#03243f"/></svg>+49 (0)000 - 123 456 78</span>
      <span class="topbar__item"><svg viewBox="0 0 6 6"><circle cx="3" cy="3" r="2.4" fill="none" stroke="#03243f" stroke-width=".6"/><path d="M3 1.6V3H4.2" fill="none" stroke="#03243f" stroke-width=".6"/></svg>Mo - Fr 9:00 - 18:00</span>
      <span class="topbar__item"><svg viewBox="0 0 6 6"><rect x=".5" y="1.3" width="5" height="3.4" fill="none" stroke="#03243f" stroke-width=".6"/><path d="M.5 1.3 3 3.2 5.5 1.3" fill="none" stroke="#03243f" stroke-width=".6"/></svg>info@veldhaus-bau.de</span>
      <span class="topbar__item"><svg viewBox="0 0 6 6"><path d="M3 5.8 1.3 3A1.9 1.9 0 1 1 4.7 3Z" fill="#03243f"/><circle cx="3" cy="2.2" r=".6" fill="#fff"/></svg>Lindenallee 12, 40000 Musterstadt</span>
    </div>
    <p class="hero__kicker" style="top:126px">PROJEKTMANAGEMENT &amp; PROJEKTSTEUERUNG</p>
    <h1 class="hero__title" style="top:144px">WIR REALISIEREN<br>BAUVORHABEN</h1>
    <div class="cards" style="top:237px">
      <article class="card"><p class="card__label">Betriebswirtschaftliche Planung</p><h2 class="card__title">STET CLITA KASD GUBERGREN NO SEA TAKIMATA SANCTUS EST LOREM</h2><p class="card__text">Lorem ipsum dolor sit amet, consetetur sadipscing elitr, sed diam nonumy eirmod tempor invidunt ut labore et dolore magna aliquyam erat, sed diam voluptua.</p><span class="card__button">WEITERLESEN</span></article>
      <article class="card"><p class="card__label">Steuerung der baulichen Umsetzung</p><h2 class="card__title">STET CLITA KASD GUBERGREN NO SEA TAKIMATA SANCTUS EST LOREM</h2><p class="card__text">Lorem ipsum dolor sit amet, consetetur sadipscing elitr, sed diam nonumy eirmod tempor invidunt ut labore et dolore magna aliquyam erat, sed diam voluptua.</p><span class="card__button">WEITERLESEN</span></article>
      <article class="card"><p class="card__label">Marketing und Vertrieb</p><h2 class="card__title">STET CLITA KASD GUBERGREN NO SEA TAKIMATA SANCTUS EST LOREM</h2><p class="card__text">Lorem ipsum dolor sit amet, consetetur sadipscing elitr, sed diam nonumy eirmod tempor invidunt ut labore et dolore magna aliquyam erat, sed diam voluptua.</p><span class="card__button">WEITERLESEN</span></article>
    </div>
    <footer class="footer">© 2017 Veldhaus Projektbau GmbH - Impressum</footer>
  </main>
</section>

<!-- Screen variant three -->
<section class="screen screen--three">
  <aside class="sidebar">
    <div class="brand"><span class="brand__name">Veldhaus</span><span class="brand__mark"></span></div>
    <ul class="nav">
      <li class="nav__item nav__item--active">HOME</li>
      <li class="nav__item">LEISTUNGEN</li>
      <li class="nav__item">ÜBER UNS<svg viewBox="0 0 4 4"><path d="M1 .5 2.8 2 1 3.5" fill="none" stroke="#888" stroke-width=".5"/></svg></li>
      <li class="nav__item">PROJEKTE<svg viewBox="0 0 4 4"><path d="M1 .5 2.8 2 1 3.5" fill="none" stroke="#888" stroke-width=".5"/></svg></li>
      <li class="nav__item">PARTNER</li>
      <li class="nav__item">KONTAKT</li>
      <li class="nav__item nav__search"><svg viewBox="0 0 4 4"><circle cx="1.6" cy="1.6" r="1.1" fill="none" stroke="#a58c45" stroke-width=".6"/><path d="M2.4 2.4 3.6 3.6" stroke="#a58c45" stroke-width=".6"/></svg>Suchen</li>
    </ul>
    <div class="social"><span class="social__dot"></span><span class="social__dot"></span><span class="social__dot"></span><span class="social__dot"></span></div>
  </aside>
  <main class="hero">
    <div class="hero__photo" role="img" aria-label="Foto: Zeichenwerkzeuge und Baupläne auf einem Tisch, unscharf und goldgelb getönt"></div>
    <div class="topbar">
      <span class="topbar__item"><svg viewBox="0 0 6 6"><path d="M1.2.6 2.2.5 2.6 1.9 2 2.4Q2.6 3.5 3.6 4L4.1 3.4 5.5 3.8 5.4 4.8Q3 5.2 1 2.6Z" fill="#03243f"/></svg>+49 (0)000 - 123 456 78</span>
      <span class="topbar__item"><svg viewBox="0 0 6 6"><circle cx="3" cy="3" r="2.4" fill="none" stroke="#03243f" stroke-width=".6"/><path d="M3 1.6V3H4.2" fill="none" stroke="#03243f" stroke-width=".6"/></svg>Mo - Fr 9:00 - 18:00</span>
      <span class="topbar__item"><svg viewBox="0 0 6 6"><rect x=".5" y="1.3" width="5" height="3.4" fill="none" stroke="#03243f" stroke-width=".6"/><path d="M.5 1.3 3 3.2 5.5 1.3" fill="none" stroke="#03243f" stroke-width=".6"/></svg>info@veldhaus-bau.de</span>
      <span class="topbar__item"><svg viewBox="0 0 6 6"><path d="M3 5.8 1.3 3A1.9 1.9 0 1 1 4.7 3Z" fill="#03243f"/><circle cx="3" cy="2.2" r=".6" fill="#fff"/></svg>Lindenallee 12, 40000 Musterstadt</span>
    </div>
    <p class="hero__kicker">PROJEKTMANAGEMENT &amp; PROJEKTSTEUERUNG</p>
    <h1 class="hero__title">WIR REALISIEREN<br>BAUVORHABEN</h1>
    <div class="cards">
      <article class="card"><p class="card__label">Betriebswirtschaftliche Planung</p><h2 class="card__title">STET CLITA KASD GUBERGREN NO SEA TAKIMATA SANCTUS EST LOREM</h2><p class="card__text">Lorem ipsum dolor sit amet, consetetur sadipscing elitr, sed diam nonumy eirmod tempor invidunt ut labore et dolore magna aliquyam erat, sed diam voluptua.</p><span class="card__button">WEITERLESEN</span></article>
      <article class="card"><p class="card__label">Steuerung der baulichen Umsetzung</p><h2 class="card__title">STET CLITA KASD GUBERGREN NO SEA TAKIMATA SANCTUS EST LOREM</h2><p class="card__text">Lorem ipsum dolor sit amet, consetetur sadipscing elitr, sed diam nonumy eirmod tempor invidunt ut labore et dolore magna aliquyam erat, sed diam voluptua.</p><span class="card__button">WEITERLESEN</span></article>
      <article class="card"><p class="card__label">Marketing und Vertrieb</p><h2 class="card__title">STET CLITA KASD GUBERGREN NO SEA TAKIMATA SANCTUS EST LOREM</h2><p class="card__text">Lorem ipsum dolor sit amet, consetetur sadipscing elitr, sed diam nonumy eirmod tempor invidunt ut labore et dolore magna aliquyam erat, sed diam voluptua.</p><span class="card__button">WEITERLESEN</span></article>
    </div>
    <footer class="footer">© 2017 Veldhaus Projektbau GmbH - Impressum</footer>
  </main>
</section>

</body>
</html>
```